Business Card Design (NEW FILES)

ATTENTION: New vector files are available. Please update your design to reflect/use the new (better resolution) logo images.

Seeking a unique and professional business card design for a commercial drone photography/videography business. The layout should feature
the logo (attached) and include the following information:
Owen Tarrick
614-502-7738
www.skylarkreelworks.example
NRD Certified Remote Pilot

Owen Tarrick

```html
<!DOCTYPE html>
<html lang="en">
<head>
<meta charset="utf-8">
<title>Skylark Reelworks Business Card</title>
<link rel="stylesheet" href="https://fonts.googleapis.com/css2?family=Open+Sans:wght@400;600;700;800&display=swap">
<style>
  :root {
    --stage: #232323;
    --orange: #ec8b56;
    --orange-deep: #d9773f;
    --navy: #1c1b4b;
    --paper: #ffffff;
  }
  * { box-sizing: border-box; margin: 0; padding: 0; }
  html, body { width: 1200px; height: 780px; overflow: hidden; }
  body {
    background: var(--stage);
    font-family: "Open Sans", Arial, sans-serif;
    position: relative;
  }
  .card {
    position: absolute;
    width: 560px;
    height: 320px;
    border-radius: 22px;
    overflow: hidden;
    box-shadow: 0 14px 30px rgba(0,0,0,0.55);
  }
  .card-back {
    left: 60px; top: 60px;
    background: var(--orange);
    display: flex; align-items: center; justify-content: center;
  }
  .back-brand {
    display: flex; align-items: center; gap: 16px;
    color: var(--orange-deep);
    font-weight: 600;
    font-size: 40px;
    line-height: 1.05;
    letter-spacing: 1px;
    text-transform: uppercase;
  }
  .back-brand .brand-dot {
    width: 34px; height: 34px; border-radius: 50%;
    background: var(--orange-deep);
    flex: none;
  }
  .card-front {
    left: 580px; top: 400px;
    background: var(--paper);
  }
  .front-bands { position: absolute; inset: 0; }
  .front-brand {
    position: absolute; left: 28px; top: 112px;
    width: 220px;
    display: flex; align-items: center; gap: 10px;
    color: var(--navy);
    font-weight: 600;
    font-size: 26px;
    text-transform: uppercase;
    letter-spacing: 0.5px;
    line-height: 1.05;
  }
  .front-brand .brand-dot {
    width: 18px; height: 18px; border-radius: 50%;
    background: var(--orange);
    flex: none;
  }
  .divider {
    position: absolute; left: 262px; top: 40px;
    width: 2px; height: 150px;
    background: var(--orange);
  }
  .contact {
    position: absolute; left: 290px; top: 28px;
    width: 250px;
    color: var(--navy);
  }
  .contact-name { font-size: 30px; font-weight: 800; line-height: 1.1; }
  .contact-name .first { color: var(--orange); }
  .contact-role { font-size: 13px; font-weight: 600; margin: 2px 0 8px 2px; }
  .contact-creds { font-size: 12px; line-height: 1.45; margin-bottom: 8px; margin-left: 2px; }
  .contact-list { list-style: none; font-size: 12.5px; line-height: 1.6; }
  .contact-list li { display: flex; align-items: center; gap: 8px; }
  .contact-list svg { width: 12px; height: 12px; flex: none; }
</style>
</head>
<body>
  <section class="card card-back" aria-label="Card back">
    <div class="back-brand"><span class="brand-dot"></span><span>Skylark<br>Reelworks</span></div>
  </section>

  <section class="card card-front" aria-label="Card front">
    <svg class="front-bands" viewBox="0 0 560 320" width="560" height="320" aria-hidden="true">
      <polygon points="300,248 560,206 560,234 300,276" fill="#1c1b4b"/>
      <polygon points="0,304 300,262 300,278 0,320" fill="#ec8b56"/>
    </svg>

    <div class="front-brand"><span class="brand-dot"></span><span>Skylark<br>Reelworks</span></div>

    <div class="divider"></div>

    <div class="contact">
      <h1 class="contact-name"><span class="first">Owen</span> Tarrick</h1>
      <p class="contact-role">Owner</p>
      <p class="contact-creds">NRD Certified Remote Pilot<br>Fully Insured</p>
      <ul class="contact-list">
        <li>
          <svg viewBox="0 0 12 12"><path d="M3 1 L5 3 L4 4.5 Q5 7 7.5 8 L9 7 L11 9 L9.5 11 Q2 10 1 2.5 Z" fill="#ec8b56"/></svg>
          614-502-7738
        </li>
        <li>
          <svg viewBox="0 0 12 12"><circle cx="6" cy="6" r="5" fill="none" stroke="#ec8b56" stroke-width="1.4"/><path d="M1 6 H11 M6 1 Q3 6 6 11 M6 1 Q9 6 6 11" fill="none" stroke="#ec8b56" stroke-width="1"/></svg>
          www.skylarkreelworks.example
        </li>
        <li>
          <svg viewBox="0 0 12 12"><rect x="1" y="2.5" width="10" height="7" fill="none" stroke="#ec8b56" stroke-width="1.4"/><path d="M1 2.5 L6 6.5 L11 2.5" fill="none" stroke="#ec8b56" stroke-width="1.2"/></svg>
          info@skylarkreelworks.example
        </li>
      </ul>
    </div>
  </section>
</body>
</html>
```